Kelvor Engineers: Why you should hire us keepsake

New design. Open to plastic cards. We are an engineering firm that designs cell phone towers and commercial buildings. Please check out our website www.kelvorstruct.com for more details. We want people to remember our card and for it to be useful if possible. We want the same look and feel on these cards to be translated to other marketing material we may need such as brochures.

Target Market(s)

Architects, Developers and Telecommunication Carriers

Industry/Entity Type

Engineering

Contact Information for Business Card

Card with our company colors, logo, and innovative design with elements related to our industry.

Font styles to use
Sans Serif

Colors
9bcb3c
abd036
0255a3

Requirements
Must have
• Sleek and hip design
Nice to have
• Bright lime green and navy coloring that pops with an innovative design.
Should not have
• A basic and boring design

```html
<!DOCTYPE html>
<html lang="en">
<head>
<meta charset="utf-8">
<title>Kelvor Engineers – Business Card</title>
<link href="https://fonts.googleapis.com/css2?family=Roboto:wght@400;500;900&family=Roboto+Condensed:wght@500&display=swap" rel="stylesheet">
<style>
  :root {
    --stage: #1f1f1f;
    --lime: #05f205;
    --navy: #012a57;
    --white: #ffffff;
    --paper: #f1f1f1;
    --ink: #3d3d3d;
  }
  html, body {
    margin: 0;
    width: 1200px;
    height: 960px;
    overflow: hidden;
    background: var(--stage);
  }
  .card {
    position: absolute;
    width: 600px;
    height: 343px;
    overflow: hidden;
    font-family: "Roboto", Arial, sans-serif;
  }
  .card p { margin: 0; }
  .card-front { left: 314px; top: 113px; background: var(--lime); }
  .card-back  { left: 311px; top: 472px; background: var(--paper); }

  .front-shape { position: absolute; inset: 0; }

  .brand-name {
    position: absolute;
    font-family: "Roboto", Arial, sans-serif;
    font-weight: 900;
    color: var(--lime);
    letter-spacing: -1px;
    line-height: 1;
  }
  .card-front .brand-name { right: 34px; top: 38px; font-size: 76px; }
  .card-back .brand-name { left: 0; right: 0; top: 121px; text-align: center; font-size: 92px; }

  .contact { position: absolute; left: 36px; top: 190px; color: var(--white); }
  .person-name {
    margin: 0 0 16px;
    font-family: "Roboto Condensed", "Arial Narrow", sans-serif;
    font-weight: 500;
    font-size: 21px;
    letter-spacing: 0.2px;
  }
  .contact-list { list-style: none; margin: 0; padding: 0; font-size: 14.5px; }
  .contact-list li { display: flex; align-items: center; height: 19px; }
  .contact-list svg { width: 13px; height: 13px; margin-right: 11px; fill: var(--white); }

  .tagline {
    position: absolute;
    left: 0; right: 0; top: 266px;
    display: flex; justify-content: center; align-items: center;
    color: var(--lime);
    font-weight: 500;
    font-size: 16px;
    line-height: 20px;
    letter-spacing: 0.2px;
  }
  .tagline::before, .tagline::after {
    content: ""; width: 30px; height: 2px; background: var(--navy); margin: 0 2px;
  }
  .locations {
    position: absolute; left: 0; right: 0; top: 287px;
    text-align: center; color: var(--ink);
    font-size: 15.5px; line-height: 20px; letter-spacing: 0.7px;
  }
</style>
</head>
<body>
  <section class="card card-front">
    <svg class="front-shape" viewBox="0 0 600 343" aria-hidden="true">
      <polygon points="156,0 600,0 600,185 462,340" fill="var(--navy)"/>
      <polyline points="156,0 462,340 600,185" fill="none" stroke="var(--white)" stroke-width="4"/>
    </svg>
    <p class="brand-name">KELVOR</p>
    <div class="contact">
      <h1 class="person-name">DANA WILCOTT RHEE</h1>
      <ul class="contact-list">
        <li><svg viewBox="0 0 24 24"><path d="M6.6 10.8a15 15 0 0 0 6.6 6.6l2.2-2.2c.3-.3.7-.4 1-.2 1.1.4 2.3.6 3.6.6.6 0 1 .4 1 1V20c0 .6-.4 1-1 1A17 17 0 0 1 3 4c0-.6.4-1 1-1h3.5c.6 0 1 .4 1 1 0 1.3.2 2.5.6 3.6.1.3 0 .7-.2 1z"/></svg>555.014.2290</li>
        <li><svg viewBox="0 0 24 24"><path d="M7 1h10a2 2 0 0 1 2 2v18a2 2 0 0 1-2 2H7a2 2 0 0 1-2-2V3a2 2 0 0 1 2-2zm0 3v14h10V4zm5 15.5a1 1 0 1 0 0 2 1 1 0 0 0 0-2z"/></svg>555.018.7731</li>
        <li><svg viewBox="0 0 24 24"><path d="M2 5h20v2l-10 6L2 7zm0 4.3 10 6 10-6V19H2z"/></svg>drhee@kelvorstruct.com</li>
        <li><svg viewBox="0 0 24 24"><circle cx="12" cy="12" r="10"/></svg>www.kelvorstruct.com</li>
      </ul>
    </div>
  </section>

  <section class="card card-back">
    <p class="brand-name">KELVOR</p>
    <p class="tagline">MULTI-DISCIPLINE ENGINEERING</p>
    <p class="locations">Marlow Point | Easthaven | Tessford | Corrine Falls</p>
  </section>
</body>
</html>
```